Marlow Sail Works President Business Card Carbon fiber catamarans

Hi.. I need a new business card design.. I am the President of a high tech yacht builder. We build Carbon Fiber go fast catamarans... Maybe we use the file I am sharing to you as the back of the card.. We need to look cool and crisp ...

Target Market(s)

Affluent People who will purchase a cool yacht

Industry/Entity Type

Custom Yacht Builder

Contact Information for Business Card

Dean Pellway , President, 731.508.2164 USA

Font styles to use
Serif

Requirements
Must have
• the clean crisp cool feel
Nice to have
• clean and crisp
Should not have
• Bold ugly

```html
<!DOCTYPE html>
<html lang="en">
<head>
<meta charset="utf-8">
<title>Marlow Sail Works — Business Card</title>
<link href="https://fonts.googleapis.com/css2?family=Cinzel:wght@400&family=Cormorant+Garamond:wght@400;500&display=swap" rel="stylesheet">
<style>
  :root {
    --backdrop: #2a2a2a;
    --card-dark: #0d0d0d;
    --card-mid: #222;
    --silver: #dcdcdc;
    --silver-soft: #a9a9a9;
    --rule: #8a8a8a;
  }
  * { margin: 0; padding: 0; box-sizing: border-box; }
  html, body { width: 1200px; height: 874px; overflow: hidden; }
  body {
    background: var(--backdrop);
    font-family: "Cormorant Garamond", serif;
    color: var(--silver);
    position: relative;
  }
  .card {
    position: absolute;
    left: 290px;
    width: 620px;
    height: 354px;
    border-radius: 4px;
    background: radial-gradient(ellipse at 50% 45%, var(--card-mid) 0%, var(--card-dark) 75%);
    box-shadow: 0 10px 30px rgba(0,0,0,.55);
    overflow: hidden;
  }
  .card-front { top: 50px; }
  .card-back { top: 470px; }

  .brand {
    position: absolute; left: 0; right: 0;
    text-align: center;
    font-family: "Cinzel", serif;
    font-weight: 400;
    font-size: 32px; letter-spacing: 4px;
    color: var(--silver);
    white-space: nowrap;
  }
  .front-brand { top: 150px; }
  .back-brand { top: 56px; }

  .social-row {
    position: absolute; bottom: 46px; left: 0; right: 0;
    display: flex; align-items: center; justify-content: center; gap: 8px;
  }
  .social-row .rule { width: 80px; height: 1px; background: var(--rule); }
  .social-dot { width: 14px; height: 14px; border-radius: 50%; background: var(--silver-soft); }

  .details {
    position: absolute; top: 150px; left: 0; right: 0;
    display: flex; justify-content: center;
  }
  .identity {
    text-align: right; padding-right: 18px;
    border-right: 1px solid var(--rule);
    font-size: 18px; line-height: 1.25; font-weight: 500;
  }
  .identity .person {
    font-family: "Cinzel", serif;
    font-size: 21px; letter-spacing: 1.5px; font-weight: 400;
  }
  .identity .role { margin-bottom: 4px; }
  .contact { list-style: none; padding-left: 18px; font-size: 18px; line-height: 1.3; font-weight: 500; }
  .contact li { display: flex; align-items: center; gap: 10px; }
  .contact svg { width: 13px; height: 13px; fill: var(--silver); flex: none; }
</style>
</head>
<body>
  <section class="card card-front">
    <div class="brand front-brand">Marlow Sail Works</div>
    <div class="social-row">
      <span class="rule"></span>
      <span class="social-dot"></span>
      <span class="social-dot"></span>
      <span class="social-dot"></span>
      <span class="rule"></span>
    </div>
  </section>

  <section class="card card-back">
    <div class="brand back-brand">Marlow Sail Works</div>
    <div class="details">
      <div class="identity">
        <div class="person">DEAN PELLWAY</div>
        <div class="role">President</div>
        <div>2140 Harbor Crest Road</div>
        <div>Juneau, Alaska 99801</div>
      </div>
      <ul class="contact">
        <li><svg viewBox="0 0 16 16"><path d="M3 1l3 3-1.5 2a9 9 0 0 0 5.5 5.5L12 10l3 3-2 2C7 15 1 9 1 3z"/></svg>731.508.2164</li>
        <li><svg viewBox="0 0 16 16"><path d="M4 0h8v16H4zM5.5 2v10h5V2zM7 13.5h2v1H7z"/></svg>731.508.2197</li>
        <li><svg viewBox="0 0 16 16"><path d="M0 3h16v10H0zM1.5 4.5 8 9l6.5-4.5"/></svg>name@marlowsail.com</li>
        <li><svg viewBox="0 0 16 16"><circle cx="8" cy="8" r="7"/></svg>www.marlowsail.com</li>
      </ul>
    </div>
  </section>
</body>
</html>
```